Penfield Draft Works (PDWorks.net)

We need a Wordpress-based site designed for a client who provides writing and editing services for the IT industry. We have a wireframe complete for the homepage, but need all internal pages designed (based on homepage wireframe) and the entire site coded for WP.

Internal pages include: "Our Work" (with samples & testimonials); "Capabilities" (with sections to address "strategy", "coaching", "writing" and "editing"); "About Us"; and a Contact page.

Will provide all copywriting, writing samples, testimonials, and client logos.

We completely realize/acknowledge the subject matter is visually BORING! Anything at all that can be done to make it look visually appealing would be *great*! Stock photography is fine.

Please feel free to ask any questions whatsoever. Thanks for your time!

```html
<!DOCTYPE html>
<html lang="en">
<head>
<meta charset="utf-8">
<title>Penfield Draft Works</title>
<link rel="stylesheet" href="https://fonts.googleapis.com/css2?family=Poppins:wght@500;600;700&family=Roboto:wght@400;500&display=swap">
<style>
:root{
  --blue:#29b6e8;
  --orange:#f26a0c;
  --peach:#fdf1ea;
  --ink:#1c1c1c;
  --text:#3a3a3a;
  --white:#fff;
  --black:#000;
}
*{margin:0;padding:0;box-sizing:border-box}
html,body{width:1200px;height:3203px;overflow:hidden;background:var(--white)}
body{position:relative;font-family:'Roboto',sans-serif;color:var(--text)}
.abs{position:absolute}
.head{font-family:'Poppins',sans-serif;font-weight:700}
.btn{position:absolute;display:flex;align-items:center;justify-content:center;background:var(--orange);color:var(--white);border-radius:22px;font-family:'Poppins',sans-serif;font-weight:600;font-size:16px}
.topbar{top:0;left:0;width:1200px;height:6px;background:var(--blue)}
.brand{left:112px;top:24px;text-align:center;line-height:1.25}
.brand .b1{font-family:'Poppins',sans-serif;font-weight:700;color:var(--blue);font-size:20px}
.brand .b2{font-size:18px;color:var(--ink)}
.nav a{position:absolute;top:40px;font-size:15px;color:var(--ink);text-decoration:none}
.hero{top:93px;left:0;width:1200px;height:622px;background:linear-gradient(100deg,#6a4a2c 0%,#8b6a3e 35%,#a58a52 60%,#8e7a48 100%)}
.hero-title{left:474px;top:262px;font-size:39px;line-height:50px;color:var(--white);text-transform:uppercase}
.hero-text{left:474px;top:368px;width:630px;font-size:16px;line-height:28px;color:var(--white)}
.sec-title{left:0;width:1200px;text-align:center;color:var(--blue);font-size:31px}
.sec-text{left:230px;width:740px;text-align:center;font-size:15.5px;line-height:28px;color:var(--ink)}
.cap{position:absolute;top:943px;width:227px;height:332px;background:var(--white);border-radius:18px;box-shadow:0 4px 14px rgba(0,0,0,.15);border-bottom:4px solid var(--blue);overflow:hidden;text-align:center}
.cap .photo{height:149px}
.cap .icon{position:absolute;left:82px;top:118px;width:62px;height:62px;border-radius:50%;background:var(--white);box-shadow:0 2px 8px rgba(0,0,0,.15);display:flex;align-items:center;justify-content:center}
.cap h3{margin-top:38px;font-family:'Poppins',sans-serif;font-weight:600;color:var(--blue);font-size:20px}
.cap p{margin:8px 12px 0;font-size:15px;line-height:24px;color:var(--ink)}
.cap.feature{top:918px;height:372px;border-bottom:none;background:linear-gradient(180deg,#e77b32,#ef8840);color:var(--white)}
.cap.feature h3{margin-top:8px;color:var(--white)}
.cap.feature p{color:#fde8d8}
.clients{top:1452px;left:0;width:1200px;height:249px;background:var(--peach)}
.logo{position:absolute;top:119px;width:141px;height:64px;background:var(--white);box-shadow:0 2px 8px rgba(0,0,0,.12);display:flex;align-items:center;justify-content:center;font-family:'Poppins',sans-serif;font-weight:600;font-size:15px;color:#555}
.work-photo{position:absolute;border-radius:12px;box-shadow:0 4px 14px rgba(0,0,0,.2)}
.work-card{position:absolute;background:var(--white);box-shadow:0 3px 12px rgba(0,0,0,.12);padding:14px 20px 0}
.work-card h4{font-family:'Poppins',sans-serif;font-weight:600;font-size:20px;color:var(--ink)}
.work-card p{margin-top:6px;font-size:15.5px;line-height:28.5px;color:var(--text)}
.work-card .more{margin-top:6px;font-family:'Poppins',sans-serif;font-weight:600;color:var(--orange);font-size:15px}
.contact-l{top:2545px;left:0;width:600px;height:480px;background:linear-gradient(180deg,#3d8fb8,#5aa6c8)}
.contact-r{top:2545px;left:600px;width:600px;height:480px;background:linear-gradient(180deg,#c45f1c,#e07a2a)}
.cta{color:var(--white);font-family:'Poppins',sans-serif;font-weight:600;font-size:28px;line-height:44px;text-align:center}
.ghost{position:absolute;border:2px solid var(--white);border-radius:22px;color:var(--white);display:flex;align-items:center;justify-content:center;font-family:'Poppins',sans-serif;font-weight:600;font-size:16px}
.email{left:669px;top:2754px;width:459px;height:65px;border:2px solid var(--white);color:var(--white);font-size:19px;padding:18px 10px}
.foot-info{top:3022px;font-size:15.5px;color:var(--white);display:flex;align-items:center;gap:10px}
.social{position:absolute;top:3071px;width:29px;height:29px;background:var(--blue);border-radius:3px}
.rule{left:112px;top:3134px;width:958px;height:1px;background:#444}
.copy{left:0;width:1200px;top:3153px;text-align:center;font-size:15px;color:var(--white)}
</style>
</head>
<body>
<div class="abs topbar"></div>

<header>
  <div class="abs brand"><div class="b1">PENFIELD DRAFT</div><div class="b2">WORKS</div></div>
  <nav class="nav">
    <a style="left:487px">Home</a>
    <a style="left:571px">About Us</a>
    <a style="left:675px">Our Work</a>
    <a style="left:781px">Capbilities</a>
    <a style="left:895px">Blog</a>
  </nav>
  <div class="btn" style="left:967px;top:32px;width:122px;height:39px">Get In Touch</div>
</header>

<section>
  <div class="abs hero" role="img" aria-label="Photo of a woman writing in a notebook while sitting in a meadow"></div>
  <svg class="abs" style="top:93px;left:0" width="1200" height="630" viewBox="0 0 1200 630">
    <path d="M0 532 Q560 705 1200 492 L1200 630 L0 630Z" fill="#29b6e8"/>
    <path d="M0 548 Q560 722 1200 518 L1200 630 L0 630Z" fill="#fff"/>
  </svg>
  <h1 class="abs head hero-title">Communicate your expertise<br>and your customer successes</h1>
  <p class="abs hero-text">Lorem ipsum dolor sit amet, consectetur adipiscing elit, sed do eiusmod tempor incididunt et dolore magna aliqua. Ut enim ad minim veniam, quis nostrud exercitation</p>
  <div class="btn" style="left:474px;top:435px;width:118px;height:38px">Learn More</div>
</section>

<section>
  <h2 class="abs head sec-title" style="top:790px">Our Capbilities</h2>
  <p class="abs sec-text" style="top:838px">Lorem ipsum dolor sit amet, consectetur adipiscing elit, sed do eiusmod tempor incididunt ut labore &nbsp;ad minim veniam, quis nostrud exercitation ullamco laboris nisi ut aliquip</p>

  <div class="cap" style="left:112px">
    <div class="photo" role="img" aria-label="Team meeting around an office table" style="background:linear-gradient(135deg,#c9a57a,#e8d9c2 60%,#b08c60)"></div>
    <div class="icon"><svg width="34" height="34" viewBox="0 0 34 34" fill="none" stroke="#f26a0c" stroke-width="2"><rect x="4" y="4" width="26" height="18"/><path d="M9 17l5-5 4 3 7-7M12 22l-4 8M22 22l4 8"/></svg></div>
    <h3>Stategy</h3>
    <p>Lorem ipsum dolor sit amet, consectetur adipiscing elit, sed do eiusmod tempor incididunt ut labore et dolore</p>
  </div>
  <div class="cap feature" style="left:362px">
    <div role="img" aria-label="Coaching session photo with orange tint" style="height:80px"></div>
    <svg width="54" height="50" viewBox="0 0 54 50" fill="none" stroke="#fff" stroke-width="2"><rect x="20" y="4" width="30" height="20"/><circle cx="10" cy="10" r="4"/><path d="M6 16h8v14H6zM24 10h20M24 15h14M14 20l6-4"/><circle cx="22" cy="36" r="3"/><circle cx="32" cy="36" r="3"/><circle cx="42" cy="36" r="3"/><path d="M18 46v-4h8v4M28 46v-4h8v4M38 46v-4h8v4"/></svg>
    <h3>Coaching</h3>
    <p>Lorem ipsum dolor sit amet, consectetur adipiscing elit, sed do eiusmod tempor incididunt ut labore et dolore</p>
  </div>
  <div class="cap" style="left:611px">
    <div class="photo" role="img" aria-label="Man writing at a desk by a window" style="background:linear-gradient(135deg,#5c4a3c,#c8b8a4 60%,#8a7664)"></div>
    <div class="icon"><svg width="34" height="34" viewBox="0 0 34 34" fill="none" stroke="#f26a0c" stroke-width="2"><path d="M6 3h16l6 6v22H6z"/><path d="M10 12h10M10 17h12M10 22h8M20 28l10-10 2 2-10 10h-2z"/></svg></div>
    <h3>Writing</h3>
    <p>Lorem ipsum dolor sit amet, consectetur adipiscing elit, sed do eiusmod tempor incididunt ut labore et dolore</p>
  </div>
  <div class="cap" style="left:861px">
    <div class="photo" role="img" aria-label="Person editing video on a laptop" style="background:linear-gradient(135deg,#2a2622,#6a5a4a 55%,#3a3430)"></div>
    <div class="icon"><svg width="34" height="34" viewBox="0 0 34 34" fill="none" stroke="#f26a0c" stroke-width="2.2"><path d="M16 6H5v23h23V18"/><path d="M25 3l6 6-14 14h-6v-6z"/></svg></div>
    <h3>Editing</h3>
    <p>Lorem ipsum dolor sit amet, consectetur adipiscing elit, sed do eiusmod tempor incididunt ut labore et dolore</p>
  </div>
  <div class="btn" style="left:502px;top:1327px;width:186px;height:40px">View Our Capbilities</div>
</section>

<section class="abs clients">
  <h2 class="abs head sec-title" style="top:40px;font-size:30px">A Selection Of Past And Current Clients</h2>
  <div class="logo" style="left:139px">Larkspur Goods</div>
  <div class="logo" style="left:341px">Harbor Crest</div>
  <div class="logo" style="left:543px">Prairie Wing</div>
  <div class="logo" style="left:745px">Keystone</div>
  <div class="logo" style="left:948px">Brightroom</div>
</section>

<section>
  <h2 class="abs head sec-title" style="top:1810px">Our Work</h2>

  <div class="work-photo" role="img" aria-label="Woman arranging sticky notes on a glass wall during a meeting" style="left:112px;top:1939px;width:298px;height:241px;background:linear-gradient(135deg,#8a9aa4,#d8dfe2 55%,#5e6a70)"></div>
  <div class="work-card" style="left:126px;top:2152px;width:270px;height:202px">
    <h4>Lorem ipsum</h4>
    <p>Duis aute irure dolor in voluptate velit esse cillum dolore eu fugiat nulla pariatur. Excepteur sint occaecat cupidatat non proident,</p>
    <div class="more">Read More &#8594;</div>
  </div>

  <div class="work-photo" role="img" aria-label="Woman writing in a notebook at a desk" style="left:443px;top:1905px;width:316px;height:308px;background:linear-gradient(135deg,#4e5e3e,#b9b6a8 55%,#6e7458)"></div>
  <div class="work-card" style="left:456px;top:2191px;width:288px;height:202px">
    <h4>Lorem ipsum</h4>
    <p>Duis aute irure dolor in voluptate velit esse cillum dolore eu fugiat nulla pariatur. Excepteur sint occaecat cupidatat non proident,</p>
    <div class="more">Read More &#8594;</div>
  </div>

  <div class="work-photo" role="img" aria-label="Editing studio with monitors and a laptop" style="left:790px;top:1939px;width:298px;height:241px;background:linear-gradient(135deg,#1e2630,#4a5a6a 50%,#8a5a30)"></div>
  <div class="work-card" style="left:805px;top:2152px;width:268px;height:202px">
    <h4>Lorem ipsum</h4>
    <p>Duis aute irure dolor in voluptate velit esse cillum dolore eu fugiat nulla pariatur. Excepteur sint occaecat cupidatat non proident,</p>
    <div class="more">Read More &#8594;</div>
  </div>

  <div class="btn" style="left:528px;top:2427px;width:144px;height:38px">View Our Work</div>
</section>

<section>
  <div class="abs contact-l" role="img" aria-label="Photo of a woman writing, tinted blue"></div>
  <div class="abs contact-r" role="img" aria-label="Photo of a man working at a computer, tinted orange"></div>
  <div class="abs cta" style="left:0;top:2640px;width:600px">Feel free to contact Us with any<br>qustions. We're happy to help</div>
  <div class="ghost" style="left:236px;top:2748px;width:125px;height:40px">Get In Touch</div>
  <div class="abs cta" style="left:600px;top:2637px;width:600px;font-size:30px">Editorial inspiration delivered<br>straight to your inbox</div>
  <div class="abs email">Email Address</div>
</section>

<footer>
  <svg class="abs" style="top:2880px;left:0" width="1200" height="323" viewBox="0 0 1200 323">
    <path d="M0 135 Q520 -40 1200 80 L1200 323 L0 323Z" fill="#000"/>
  </svg>
  <div class="abs brand" style="left:0;width:1200px;top:2950px">
    <div class="b1">PENFIELD DRAFT</div><div class="b2" style="color:#fff">WORKS</div>
  </div>
  <div class="abs foot-info" style="left:275px">
    <svg width="12" height="16" viewBox="0 0 12 16"><path d="M6 0a6 6 0 0 0-6 6c0 4.5 6 10 6 10s6-5.5 6-10a6 6 0 0 0-6-6zm0 8.5A2.5 2.5 0 1 1 6 3.5a2.5 2.5 0 0 1 0 5z" fill="#fff"/></svg>
    Lorem ipsum dolor 12345
  </div>
  <div class="abs foot-info" style="left:548px">
    <svg width="14" height="14" viewBox="0 0 24 24"><path d="M6.6 10.8a15 15 0 0 0 6.6 6.6l2.2-2.2a1 1 0 0 1 1-.25 11.4 11.4 0 0 0 3.6.57 1 1 0 0 1 1 1V20a1 1 0 0 1-1 1A17 17 0 0 1 3 4a1 1 0 0 1 1-1h3.5a1 1 0 0 1 1 1c0 1.25.2 2.45.57 3.6a1 1 0 0 1-.25 1z" fill="#fff"/></svg>
    123 456 7890
  </div>
  <div class="abs foot-info" style="left:747px">
    <svg width="16" height="13" viewBox="0 0 16 13" fill="none" stroke="#fff" stroke-width="1.6"><rect x="1" y="1" width="14" height="11" rx="1"/><path d="M1 2l7 5 7-5"/></svg>
    info@pdworks.net
  </div>
  <div class="social" style="left:521px" aria-label="Social link"></div>
  <div class="social" style="left:563px" aria-label="Social link"></div>
  <div class="social" style="left:607px" aria-label="Social link"></div>
  <div class="social" style="left:649px" aria-label="Social link"></div>
  <div class="abs rule"></div>
  <div class="abs copy">&copy;&nbsp; Copyrights 2021 pdworks | All Rights Reserved</div>
</footer>
</body>
</html>
```